SkyvornQ Business Cards and Stationary Design

Need a design for our business cards and stationary. I want to carry on the theme of the logo. I want the business cards to have a design on the back. I would like the business cards and the stationary to carry the same theme, design scheme, and branding

Target Market(s)

Airlines and Maintenance Facilities

Industry/Entity Type

Aviation

Contact Information for Business Card

Name
Position Title
Address: 4827 Trellis Hollow Road, Wrenfield Cove, Brantmoor, 34951
Office Number
Mobile Number
Email
Website

Font styles to use
Serif
Sans Serif

Colors

Designer to choose colors to be used in the design.

```html
<!DOCTYPE html>
<html lang="en">
<head>
<meta charset="utf-8">
<title>SkyvornQ Business Card</title>
<link rel="stylesheet" href="https://fonts.googleapis.com/css2?family=Roboto:wght@400;500;700&family=Roboto+Condensed:wght@500;700&display=swap">
<style>
  :root {
    --stage: #e9ebef;
    --paper: #ffffff;
    --navy: #0d2a5c;
    --navy-deep: #061a3f;
    --sky: #1c9ae0;
    --ink: #3a3f48;
    --web-light: #dfe7f5;
  }
  * { box-sizing: border-box; margin: 0; padding: 0; }
  html, body { width: 1200px; height: 911px; overflow: hidden; }
  body {
    background: var(--stage);
    font-family: "Roboto", Arial, sans-serif;
    position: relative;
  }
  .card {
    position: absolute;
    width: 560px;
    height: 320px;
    border-radius: 18px;
    box-shadow: 0 10px 28px rgba(10, 25, 60, 0.18);
    overflow: hidden;
  }
  /* Front */
  .card-front {
    left: 50px;
    top: 110px;
    background: var(--paper);
  }
  .front-tab {
    position: absolute;
    right: 26px;
    top: 0;
    width: 28px;
    height: 12px;
    background: linear-gradient(180deg, var(--navy), var(--sky));
  }
  .front-brand {
    position: absolute;
    left: 36px;
    top: 130px;
    display: flex;
    align-items: center;
    gap: 14px;
  }
  .brand-dot {
    flex: none;
    width: 44px;
    height: 44px;
    border-radius: 50%;
    background: var(--sky);
  }
  .brand-name {
    font-family: "Roboto", Arial, sans-serif;
    font-weight: 700;
    letter-spacing: 3px;
    text-transform: uppercase;
    white-space: nowrap;
  }
  .front-brand .brand-name { font-size: 28px; color: var(--navy); }
  .front-details {
    position: absolute;
    right: 32px;
    top: 30px;
    width: 240px;
    text-align: right;
  }
  .person-name {
    font-family: "Roboto Condensed", Arial, sans-serif;
    font-weight: 700;
    font-size: 22px;
    color: var(--navy);
    letter-spacing: 0.5px;
  }
  .person-role {
    font-family: "Roboto Condensed", Arial, sans-serif;
    font-weight: 500;
    font-size: 14px;
    color: var(--sky);
    margin-top: 2px;
  }
  .contact-list {
    list-style: none;
    margin-top: 22px;
    font-size: 12px;
    line-height: 18px;
    color: var(--ink);
  }
  .contact-list li { display: flex; justify-content: flex-end; align-items: center; gap: 6px; white-space: nowrap; }
  .contact-list svg { width: 11px; height: 11px; fill: var(--navy); flex: none; }
  .front-wordmark {
    position: absolute;
    right: 32px;
    bottom: 30px;
    font-size: 26px;
    color: var(--navy);
    letter-spacing: 4px;
  }
  /* Back */
  .card-back {
    left: 600px;
    top: 470px;
    background: radial-gradient(ellipse at 55% 45%, var(--navy) 0%, var(--navy-deep) 80%);
  }
  .back-brand {
    position: absolute;
    left: 0; right: 0;
    top: 118px;
    display: flex;
    justify-content: center;
    align-items: center;
    gap: 18px;
  }
  .back-brand .brand-name { font-size: 36px; color: #ffffff; letter-spacing: 5px; }
  .back-brand .brand-dot { width: 46px; height: 46px; }
  .back-web {
    position: absolute;
    left: 0; right: 0;
    bottom: 44px;
    text-align: center;
    color: var(--web-light);
    font-size: 12px;
    letter-spacing: 5px;
  }
</style>
</head>
<body>
  <section class="card card-front" aria-label="Business card front">
    <div class="front-tab"></div>
    <div class="front-brand">
      <span class="brand-dot"></span>
      <span class="brand-name">SkyvornQ</span>
    </div>
    <div class="front-details">
      <p class="person-name">DORIAN KELLER</p>
      <p class="person-role">CEO/FOUNDER</p>
      <ul class="contact-list">
        <li>4827 Trellis Hollow Road</li>
        <li>Wrenfield Cove, Brantmoor, 34951</li>
        <li>555 214 7083
          <svg viewBox="0 0 12 12"><path d="M3 1l2 2-1 1.5c.6 1.4 1.8 2.6 3.2 3.2L8.7 6.7l2 2-1.4 1.8C5.5 10.2 1.8 6.5 1.4 2.7z"/></svg>
        </li>
        <li>555 389 6120
          <svg viewBox="0 0 12 12"><path d="M3.5 0.5h5a1 1 0 0 1 1 1v9a1 1 0 0 1-1 1h-5a1 1 0 0 1-1-1v-9a1 1 0 0 1 1-1zm.3 1.3v7.4h4.4V1.8z"/></svg>
        </li>
        <li>info@skyvornq.com
          <svg viewBox="0 0 12 12"><path d="M1 2.5h10v7H1zm1 1v.4l4 2.6 4-2.6v-.4zm0 1.6v3.4h8V5.1L6 7.7z"/></svg>
        </li>
        <li>www.skyvornq.com
          <svg viewBox="0 0 12 12"><circle cx="6" cy="6" r="5"/></svg>
        </li>
      </ul>
    </div>
    <p class="brand-name front-wordmark">SkyvornQ</p>
  </section>

  <section class="card card-back" aria-label="Business card back">
    <div class="back-brand">
      <span class="brand-name">SkyvornQ</span>
      <span class="brand-dot"></span>
    </div>
    <p class="back-web">www.skyvornq.com</p>
  </section>
</body>
</html>
```